Brookvale Estates LLC stationary for a real estate property management company.

Create stationary (letterhead, envelopes, business cards) using Brookvale Estates LLC logo as primary creative element. Stationary design needs to be horizontal, leaving as much space as possible for correspondence copy. See attached Creative Brief and past stationary files for details.

Target Market(s)

Prospective apartment residents and current residents, vendors, and government agencies.

Industry/Entity Type

Property Management

Contact Information for Business Card

Business card employee title: Property Manager. Should include address, phone, fax, email, website, slogan, and Brookvale Estates logo.

Font styles to use
Sans Serif

Colors
0592cd
000000

Requirements
Must have
• Tone should be conservative, institutional, business (i.e. banking, finance, real estate). Must include: address, phone, fax, website, and slogan (see attached Creative Brief). Should be a horizontal design, leaving as much room as possible for letter correspondence copy.
Nice to have
• Please use an Arial or Helvetica style font.
Should not have
• Letterhead layout should leave as much room as possible for copy.

```html
<!DOCTYPE html>
<html lang="en">
<head>
<meta charset="utf-8">
<title>Brookvale Estates LLC — Stationery</title>
<link href="https://fonts.googleapis.com/css2?family=Arimo:wght@400;700&display=swap" rel="stylesheet">
<style>
:root{
  --brand:#1b75b1;
  --charcoal:#58595b;
  --ink:#333;
  --paper:#fff;
  --backdrop:#ececec;
}
*{margin:0;padding:0;box-sizing:border-box}
html,body{width:1200px;height:938px;overflow:hidden}
body{background:var(--backdrop);font-family:"Arimo",Arial,sans-serif;color:var(--ink);position:relative}
.sheet{position:absolute;background:var(--paper);overflow:hidden}
.brand{position:absolute;display:flex;align-items:center;gap:6px;color:var(--brand);font-weight:700;line-height:1}
.brand-mark{background:var(--brand);flex:none}
.brand-name{display:flex;flex-direction:column}
.brand-name .sub{letter-spacing:.18em}
.band{position:absolute;display:flex;gap:3px}
.band .grey{background:var(--charcoal)}
.band .blue{background:var(--brand);color:#fff;display:flex;align-items:center;justify-content:center;letter-spacing:.06em}
.contact{position:absolute;font-size:4.6px;line-height:8px;color:#555}
.contact li{list-style:none;display:flex;align-items:center;gap:3px}
.contact i{display:inline-block;width:5px;height:5px;background:#333}
/* letterhead */
.letterhead{left:184px;top:68px;width:388px;height:544px}
.letter-body{position:absolute;left:38px;top:138px;width:295px;font-size:5.2px;line-height:8.6px;color:#444}
.letter-body p{margin-bottom:8px}
.letter-body .gap{margin-bottom:24px}
.signature{width:40px;height:24px;background:linear-gradient(#f4f4f4,#e6e6e6);margin:6px 0}
/* folder */
.folder{left:637px;top:40px;width:457px;height:576px}
/* cards */
.card-front{left:46px;top:661px;width:176px;height:97px}
.card-back{left:46px;top:786px;width:176px;height:99px}
.holder{position:absolute;left:122px;top:17px;font-size:6.4px;line-height:8px;letter-spacing:.04em}
.holder small{display:block;font-size:4.4px}
/* envelopes */
.envelope-front{left:266px;top:674px;width:431px;height:208px}
.envelope-back{left:737px;top:674px;width:432px;height:206px}
.flap{position:absolute;left:0;top:0;width:100%;height:70px;background:var(--brand);border-radius:0 0 40px 40px;color:#fff;font-size:14px;letter-spacing:.06em;display:flex;align-items:center;justify-content:center}
</style>
</head>
<body>

<section class="sheet letterhead">
  <div class="brand" style="left:20px;top:26px">
    <span class="brand-mark" style="width:18px;height:22px"></span>
    <span class="brand-name"><span style="font-size:14px">BROOKVALE</span><span class="sub" style="font-size:6px;margin-top:2px">ESTATES LLC</span></span>
  </div>
  <div class="letter-body">
    <p style="margin-bottom:6px">July 2, 2012</p>
    <p><b>Dear CH,</b><br>Oak House, Elm St., Fairview</p>
    <p class="gap">is simply dummy text of the printing and typesetting industry. Lorem Ipsum has been the industry's standard dummy text ever since the 1500s, when an unknown printer took a galley of type and scrambled it to make a type specimen book. It has survived not only five centuries, but also the leap into electronic typesetting, remaining essentially unchanged. It was popularised in the 1960s with the release of transfer sheets containing Lorem Ipsum passages, and more recently with desktop publishing and layout tools including versions of Lorem Ipsum.</p>
    <p class="gap">is simply dummy text of the printing and typesetting industry. Lorem Ipsum has been the industry's standard dummy text ever since the 1500s, when an unknown printer took a galley of type and scrambled it to make</p>
    <p>is simply dummy text of the printing and typesetting industry. Lorem Ipsum has been the industry's standard dummy text ever since the 1500s, when an unknown printer took a galley of type and scrambled it to make a type specimen book. It has survived not only five centuries, but also the leap into electronic typesetting, remaining essentially unchanged. It was popularised in the 1960s with the release of transfer sheets containing Lorem Ipsum passages, and more recently with desktop publishing and layout tools including versions of Lorem Ipsum.</p>
    <p style="margin-bottom:0">Best Regards,</p>
    <div class="signature" role="img" aria-label="Handwritten signature"></div>
    <p><b>Daniel Hart</b><br>Director<br><span style="display:block;margin-top:3px">Oak House, Elm St., Fairview</span></p>
  </div>
  <div class="band" style="left:0;top:487px;width:388px;height:16px">
    <span class="grey" style="width:118px"></span>
    <span class="blue" style="flex:1;font-size:9px">www.brookvaleestates.com</span>
  </div>
  <ul class="contact" style="left:9px;top:512px">
    <li><i></i>Street country 123</li><li><i></i>014 552 7310</li><li><i></i>info@brookvale.com</li>
  </ul>
  <ul class="contact" style="left:318px;top:512px">
    <li><i></i>www.brookvaleestates.com</li><li><i></i>www.brookvale.com/news</li><li><i></i>www.brookvale.com/blog</li>
  </ul>
</section>

<section class="sheet folder">
  <div class="brand" style="left:88px;top:250px;gap:12px">
    <span class="brand-mark" style="width:54px;height:66px"></span>
    <span class="brand-name"><span style="font-size:40px">BROOKVALE</span><span class="sub" style="font-size:15px;margin-top:5px">ESTATES LLC</span></span>
  </div>
  <div class="band" style="left:0;top:524px;width:457px;height:28px">
    <span class="grey" style="width:139px"></span>
    <span class="blue" style="flex:1;font-size:13px">www.brookvaleestates.com</span>
  </div>
</section>

<section class="sheet card-front">
  <div class="brand" style="left:8px;top:10px;gap:4px">
    <span class="brand-mark" style="width:12px;height:16px"></span>
    <span class="brand-name"><span style="font-size:11px">BROOKVALE</span><span class="sub" style="font-size:4.5px;margin-top:1px">ESTATES LLC</span></span>
  </div>
  <div class="holder">ALAN REED<small>PROPERTY MANAGER</small></div>
  <div class="band" style="left:0;top:41px;width:176px;height:16px">
    <span class="grey" style="width:54px"></span>
    <span class="blue" style="flex:1;font-size:5.6px">www.brookvaleestates.com/123</span>
  </div>
  <ul class="contact" style="left:9px;top:66px;font-size:4px">
    <li><i></i>Street country 123</li><li><i></i>014 552 7310</li><li><i></i>info@brookvale.com</li>
  </ul>
  <ul class="contact" style="left:100px;top:66px;font-size:4px">
    <li><i></i>www.brookvaleestates.com</li><li><i></i>www.brookvale.com/news</li><li><i></i>www.brookvale.com/blog</li>
  </ul>
</section>

<section class="sheet card-back">
  <div class="brand" style="left:46px;top:36px;gap:4px">
    <span class="brand-mark" style="width:12px;height:16px"></span>
    <span class="brand-name"><span style="font-size:11px">BROOKVALE</span><span class="sub" style="font-size:4.5px;margin-top:1px">ESTATES LLC</span></span>
  </div>
</section>

<section class="sheet envelope-front">
  <div class="brand" style="left:14px;top:22px;gap:5px">
    <span class="brand-mark" style="width:17px;height:22px"></span>
    <span class="brand-name"><span style="font-size:15px">BROOKVALE</span><span class="sub" style="font-size:6.5px;margin-top:2px">ESTATES LLC</span></span>
  </div>
  <div class="band" style="left:0;top:164px;width:431px;height:19px">
    <span class="grey" style="width:131px"></span>
    <span class="blue" style="flex:1;font-size:10px">www.brookvaleestates.com</span>
  </div>
</section>

<section class="sheet envelope-back">
  <div class="flap">www.brookvaleestates.com</div>
</section>

</body>
</html>
```